Creation of brand identity and website "Tandem K"

I am currently seeking an brand, identity and web design for a new project called Tandem K. This is a brand new concept from scratch and you have free-reign on the whole design process, taking into account my preference below.

Must include the name "Tandem K", or "Tandem K: Or the year I woke Up". Kudos is this forms part of the brands logo

Design that can be easily scaled to potentially include: a blog, timeline and vlogs.

Minimal but effective use of colour (however any colours and combinations permitted

Use of icons/graphics over text wherever possible

Minimal use of frames and borders

I appreciate this is a fairly wide scope so please contact me on marblefinch@postwillow.com with any questions or more information on what the project is.

Target Market(s)

Male and Female 20-40
Blog readers
Selfhelp

Industry/Entity Type

Seeking

Number of Pages Required

1 page

Font styles to use
Serif
Sans Serif

Requirements
Must have
• It is in effect a blog design, so about me section, recent blog / archived posts, reader comments / Q and A section.
• A coded design would be appreciated to make my life easier however I have left the design as uncoded as getting the right design matters more to me and I want to keep the project open to as many designers as possible
Nice to have
• See project description for other details and please ask if you need anything else :)
Should not have
• Mustn't be cluttered or feel fussy
• Promote icons over text
• Frames / multiple borders

```html
<!DOCTYPE html>
<html lang="en">
<head>
<meta charset="utf-8">
<title>Tandem K – Blog</title>
<link href="https://fonts.googleapis.com/css2?family=Montserrat:wght@500;600;700&family=Lato:wght@400;700&display=swap" rel="stylesheet">
<style>
:root{
  --navy:#263a5e;
  --orange:#ef4423;
  --text:#5a5f66;
  --rule:#d9d9d9;
  --band:#ebebeb;
  --white:#ffffff;
}
*{box-sizing:border-box;margin:0;padding:0}
html,body{width:687px;height:1200px;overflow:hidden;background:var(--white)}
body{position:relative;font-family:"Lato",sans-serif;color:var(--text);font-size:9px;line-height:1.45}
.abs{position:absolute}
h1,h2,h3,h4,.nav a,.btn,.widget-title{font-family:"Montserrat",sans-serif}
.brand{left:69px;top:10px;font-size:19px;font-weight:700;color:var(--navy);letter-spacing:.3px}
.search{display:flex;border:1px solid var(--navy)}
.search span{flex:1;padding:1px 6px;color:#8a8f96;font-size:9.5px}
.search i{width:36px;background:var(--orange);display:flex;align-items:center;justify-content:center}
.top-search{left:427px;top:14px;width:192px;height:18px}
.navbar{left:0;top:46px;width:687px;height:27px;background:var(--navy)}
.nav{position:absolute;left:69px;top:0;display:flex;height:27px}
.nav a{color:var(--white);text-decoration:none;font-size:8.5px;font-weight:600;padding:0 11px;line-height:27px}
.nav a.active{background:var(--orange);padding:0 12px}
.social{position:absolute;right:69px;top:7px;display:flex;gap:6px}
.social span{width:13px;height:13px;border-radius:50%;background:var(--orange)}
.photo{display:block}
.meta{font-size:8px;color:var(--navy);display:flex;align-items:center;gap:3px;letter-spacing:.2px}
.meta b{font-weight:700}
.meta svg{flex:none}
h2{font-size:14px;font-weight:600;color:var(--navy);letter-spacing:.3px}
h3{font-size:11.5px;font-weight:600;color:var(--navy);line-height:1.35;letter-spacing:0;white-space:nowrap}
.btn{display:inline-block;border:1px solid var(--orange);color:var(--orange);font-size:8px;font-weight:700;padding:0;width:70px;height:21px;line-height:19px;text-align:center}
.rule{height:1px;background:var(--rule)}
.hero-caption{left:234px;top:223px;color:var(--white);font-family:"Montserrat",sans-serif;font-weight:600;font-size:13px}
.hero-arrows{left:383px;top:256px;display:flex;gap:12px}
.load-more{left:69px;top:940px;width:358px;height:25px;background:#cfcfcf;display:flex;align-items:center;justify-content:center;gap:6px;color:#333;font-size:8.5px}
.widget-title{left:448px;width:170px;height:20px;background:var(--orange);color:var(--white);font-size:11px;font-weight:700;padding-left:7px;line-height:20px;border-right:2px solid var(--navy);letter-spacing:.4px}
.widget-title em{font-style:normal;color:#fbd3c8}
.pop{display:flex;align-items:center;gap:12px;width:170px;left:448px}
.pop .dot{width:53px;height:53px;border-radius:50%;flex:none}
.pop h4{font-size:8px;color:var(--navy);font-weight:700;letter-spacing:.4px;margin-bottom:4px}
.pop p{font-size:7.5px;color:#444;line-height:1.3}
.tags{left:448px;top:681px;width:176px;display:flex;flex-wrap:wrap;gap:5px 4px}
.tags span{background:var(--navy);color:var(--white);font-size:6.5px;padding:3px 5px;letter-spacing:0;line-height:1.3}
.archive{left:448px;top:812px;list-style:none}
.archive li{display:flex;align-items:center;gap:9px;height:21.7px;font-family:"Montserrat",sans-serif;font-weight:600;font-size:10px;color:var(--navy);text-decoration:underline}
.about{left:0;top:982px;width:687px;height:184px;background:var(--band)}
.about h2{font-size:19px}
.footer{left:0;top:1166px;width:687px;height:34px;background:var(--navy);color:var(--white);text-align:center;line-height:34px;font-size:8.5px;font-weight:700}
</style>
</head>
<body>

<header>
  <div class="abs brand">Tandem K</div>
  <div class="abs search top-search"><span>Search</span><i><svg width="9" height="9" viewBox="0 0 10 10"><circle cx="4" cy="4" r="3" fill="none" stroke="#fff" stroke-width="1.5"/><path d="M6.3 6.3L9 9" stroke="#fff" stroke-width="1.5"/></svg></i></div>
  <nav class="abs navbar">
    <div class="nav"><a class="active">About Me</a><a>Recent Blog</a><a>Reader Comments</a><a>Contact Us</a></div>
    <div class="social"><span></span><span></span><span></span><span></span></div>
  </nav>
</header>

<main>
  <div class="abs photo" role="img" aria-label="Man sitting in sunlit grass with arms raised" style="left:69px;top:79px;width:358px;height:200px;background:linear-gradient(160deg,#d9b51e 0%,#9ca22a 40%,#5c7a1e 75%,#3f5a17 100%)"></div>
  <div class="abs hero-caption">Lorem Ipsum Dolor Sit Amet</div>
  <div class="abs hero-arrows">
    <svg width="8" height="12" viewBox="0 0 8 12"><path d="M6 1L1 6l5 5" fill="none" stroke="#fff" stroke-width="1.6"/></svg>
    <svg width="8" height="12" viewBox="0 0 8 12"><path d="M2 1l5 5-5 5" fill="none" stroke="#fff" stroke-width="1.6"/></svg>
  </div>
  <div class="abs meta" style="left:69px;top:290px"><svg width="9" height="9" viewBox="0 0 10 10"><circle cx="5" cy="5" r="4" fill="none" stroke="#ef4423"/><path d="M5 2.5V5h2" fill="none" stroke="#ef4423"/></svg>JULY 02, 2016 &nbsp;|&nbsp; BY &nbsp;<b>Lorem Ipsum</b></div>
  <h2 class="abs" style="left:70px;top:307px">Lorem Ipsum Dolor Sit Amet</h2>
  <p class="abs" style="left:70px;top:329px;width:355px">Lorem ipsum dolor sit amet, consectetuer adipiscing elit, sed diam nonummy nibh euismod tincidunt ut laoreet dolore magna aliquam erat volutpat.</p>
  <a class="abs btn" style="left:69px;top:362px">READ MORE</a>
  <div class="abs rule" style="left:69px;top:402px;width:358px"></div>

  <div class="abs photo" role="img" aria-label="Woman in white dress with arms open in soft sunlight" style="left:69px;top:421px;width:167px;height:108px;background:linear-gradient(120deg,#7fd1a9,#d9e39a 50%,#f4d9b0)"></div>
  <div class="abs meta" style="left:69px;top:539px;font-size:7.5px"><svg width="9" height="9" viewBox="0 0 10 10"><circle cx="5" cy="5" r="4" fill="none" stroke="#ef4423"/><path d="M5 2.5V5h2" fill="none" stroke="#ef4423"/></svg>JULY 02, 2016 | BY <b>Lorem Ipsum</b></div>
  <h2 class="abs" style="left:70px;top:557px;font-size:13px">Lorem Ipsum Dolor Sit.</h2>
  <p class="abs" style="left:70px;top:579px;width:165px">Lorem ipsum dolor sit amet, cetuer adipiscing elit.</p>
  <a class="abs btn" style="left:69px;top:612px">READ MORE</a>

  <div class="abs photo" role="img" aria-label="Silhouette with raised arms against a sunset sky" style="left:259px;top:421px;width:168px;height:108px;background:linear-gradient(180deg,#5f8fc4 0%,#e2b25a 55%,#3a2a22 100%)"></div>
  <div class="abs meta" style="left:259px;top:539px;font-size:7.5px"><svg width="9" height="9" viewBox="0 0 10 10"><circle cx="5" cy="5" r="4" fill="none" stroke="#ef4423"/><path d="M5 2.5V5h2" fill="none" stroke="#ef4423"/></svg>JULY 02, 2016 | BY <b>Lorem Ipsum</b></div>
  <h2 class="abs" style="left:259px;top:557px;font-size:13px">Lorem Ipsum Dolor Sit.</h2>
  <p class="abs" style="left:259px;top:579px;width:165px">Lorem ipsum dolor sit amet, cetuer adipiscing elit.</p>
  <a class="abs btn" style="left:259px;top:612px">READ MORE</a>
  <div class="abs rule" style="left:69px;top:652px;width:358px"></div>

  <div class="abs meta" style="left:69px;top:669px"><svg width="9" height="9" viewBox="0 0 10 10"><circle cx="5" cy="5" r="4" fill="none" stroke="#ef4423"/><path d="M5 2.5V5h2" fill="none" stroke="#ef4423"/></svg>JULY 02, 2016 &nbsp;|&nbsp; BY &nbsp;<b>Lorem Ipsum</b></div>
  <div class="abs photo" role="img" aria-label="Girl dancing on a path through a yellow flower field" style="left:69px;top:687px;width:163px;height:91px;background:linear-gradient(180deg,#9db6d6 0%,#c9c5a0 40%,#b8a828 65%,#4d5a22 100%)"></div>
  <h3 class="abs" style="left:242px;top:685px">Lorem ipsum dolor sit amet,<br>consectetuer adipiscing elit</h3>
  <p class="abs" style="left:242px;top:723px;width:185px">Lorem ipsum dolor sit amet, consectetue adipiscing elit, sed diam nonummy nibh.</p>
  <a class="abs btn" style="left:242px;top:757px">READ MORE</a>
  <div class="abs rule" style="left:69px;top:798px;width:358px"></div>

  <div class="abs meta" style="left:69px;top:813px;font-size:7.5px"><svg width="9" height="9" viewBox="0 0 10 10"><circle cx="5" cy="5" r="4" fill="none" stroke="#ef4423"/><path d="M5 2.5V5h2" fill="none" stroke="#ef4423"/></svg>JULY 02, 2016 &nbsp;|&nbsp; BY &nbsp;<b>Lorem Ipsum</b></div>
  <div class="abs photo" role="img" aria-label="Two people jumping in a meadow at sunrise" style="left:69px;top:830px;width:163px;height:92px;background:linear-gradient(180deg,#cfe0ee 0%,#f3e7b5 45%,#8c9a48 70%,#3d4a1e 100%)"></div>
  <h3 class="abs" style="left:242px;top:828px">Lorem ipsum dolor sit amet,<br>consectetuer adipiscing elit</h3>
  <p class="abs" style="left:242px;top:865px;width:185px">Lorem ipsum dolor sit amet, consectetue adipiscing elit, sed diam nonummy nibh.</p>
  <a class="abs btn" style="left:242px;top:899px">READ MORE</a>

  <div class="abs load-more"><svg width="10" height="10" viewBox="0 0 10 10"><g stroke="#ef4423" stroke-width="1.3"><path d="M5 0.5v2.2M5 7.3v2.2M0.5 5h2.2M7.3 5h2.2M1.8 1.8l1.5 1.5M6.7 6.7l1.5 1.5M1.8 8.2l1.5-1.5M6.7 3.3l1.5-1.5"/></g></svg>Load More Blog</div>
</main>

<aside>
  <div class="abs widget-title" style="top:80px">NEWSLETTER <em>SIGNUP</em></div>
  <p class="abs" style="left:448px;top:106px">Lorem Ipsum Dolor Sit Amet.</p>
  <div class="abs search" style="left:448px;top:128px;width:170px;height:16px"><span>Search...</span><i style="width:25px"><svg width="8" height="8" viewBox="0 0 10 10"><circle cx="4" cy="4" r="3" fill="none" stroke="#fff" stroke-width="1.5"/><path d="M6.3 6.3L9 9" stroke="#fff" stroke-width="1.5"/></svg></i></div>
  <div class="abs rule" style="left:448px;top:162px;width:170px"></div>

  <div class="abs photo" role="img" aria-label="Advert: climber on a cliff against an evening sky with a motivational quote" style="left:448px;top:182px;width:170px;height:137px;background:linear-gradient(180deg,#2f4f86 0%,#7a8fba 45%,#d9a98a 80%,#3a3c55 100%)"></div>
  <div class="abs" style="left:570px;top:308px;width:48px;height:11px;background:var(--navy);color:#fff;font-size:6px;text-align:center;line-height:11px">Ads by Placely</div>

  <div class="abs widget-title" style="top:356px">MOST <em>POPULAR</em>
    <svg style="position:absolute;right:6px;top:5px" width="24" height="10" viewBox="0 0 24 10"><circle cx="5" cy="5" r="4.2" fill="none" stroke="#fff"/><path d="M6 3L4 5l2 2" fill="none" stroke="#fff"/><circle cx="17" cy="5" r="4.2" fill="none" stroke="#fff"/><path d="M16 3l2 2-2 2" fill="none" stroke="#fff"/></svg>
  </div>
  <div class="abs pop" style="top:390px"><div class="dot" role="img" aria-label="Person with arms raised over a green field" style="background:linear-gradient(180deg,#4f86c6,#a7c15a)"></div><div><h4>LOREM IPSUM DOLOR</h4><p>Phasellus eget luctus metus. Vestibulum bibendum...</p></div></div>
  <div class="abs rule" style="left:448px;top:458px;width:170px"></div>
  <div class="abs pop" style="top:474px"><div><h4>LOREM IPSUM DOLOR</h4><p>Phasellus eget luctus metus. Vestibulum bibendum...</p></div><div class="dot" role="img" aria-label="Man standing in a meadow facing the sky" style="background:linear-gradient(180deg,#9fbfe0,#6f8e3a)"></div></div>
  <div class="abs rule" style="left:448px;top:544px;width:170px"></div>
  <div class="abs pop" style="top:554px"><div class="dot" role="img" aria-label="Smiling woman outdoors in warm light" style="background:linear-gradient(160deg,#f2e2c6,#c99a6a)"></div><div><h4>LOREM IPSUM DOLOR</h4><p>Phasellus eget luctus metus. Vestibulum bibendum...</p></div></div>
  <div class="abs rule" style="left:448px;top:628px;width:170px"></div>

  <div class="abs widget-title" style="top:646px">TAGS</div>
  <div class="abs tags"><span>LOREM</span><span>LOREM IPSU</span><span>REM IPSU DOLOR</span><span>LOREM IPSU</span><span>REM IPSU</span><span>LOREM DOL</span><span>LOREM IPSUM DO</span><span>REM IPSU</span></div>
  <div class="abs" style="left:448px;top:756px;width:170px;height:1px;background:var(--navy)"></div>

  <div class="abs widget-title" style="top:775px">ARCHIVE</div>
  <ul class="abs archive">
    <li><svg width="5" height="8" viewBox="0 0 5 8"><path d="M1 1l3 3-3 3" fill="none" stroke="#263a5e"/></svg>JULY 2016</li>
    <li><svg width="5" height="8" viewBox="0 0 5 8"><path d="M1 1l3 3-3 3" fill="none" stroke="#263a5e"/></svg>JUNE 2016</li>
    <li><svg width="5" height="8" viewBox="0 0 5 8"><path d="M1 1l3 3-3 3" fill="none" stroke="#263a5e"/></svg>MAY 2016</li>
    <li><svg width="5" height="8" viewBox="0 0 5 8"><path d="M1 1l3 3-3 3" fill="none" stroke="#263a5e"/></svg>APR 2016</li>
    <li><svg width="5" height="8" viewBox="0 0 5 8"><path d="M1 1l3 3-3 3" fill="none" stroke="#263a5e"/></svg>MARCH 2016</li>
    <li><svg width="5" height="8" viewBox="0 0 5 8"><path d="M1 1l3 3-3 3" fill="none" stroke="#263a5e"/></svg>FEB 2016</li>
    <li><svg width="5" height="8" viewBox="0 0 5 8"><path d="M1 1l3 3-3 3" fill="none" stroke="#263a5e"/></svg>JAN 2016</li>
  </ul>
</aside>

<section class="abs about">
  <div class="abs photo" role="img" aria-label="Portrait of the author in a blue shirt" style="left:69px;top:13px;width:157px;height:157px;border:2px solid #c9c9c9;background:linear-gradient(180deg,#8a99ab,#5f6f85 60%,#2d4272)"></div>
  <h2 class="abs" style="left:249px;top:12px">About Me</h2>
  <p class="abs" style="left:249px;top:40px;width:370px;line-height:1.38;letter-spacing:.45px">Lorem ipsum dolor sit amet, consectetuer adipiscing elit, sed diam nonummy nibh euismod alme tincidunt ut laoreet dolore magna aliquam erat volutpat. Ut wisi enim ad minim veniam, quis dol nostrud exerci tation ullamcorper suscipit lobortis nisl ut aliquip ex ea commodo consequat list Duis autem vel eum iriure dolor in hendrerit in vulputate velit esse molestie consequat, vel alm illum dolore eu feugiat nulla facilisis at vero eros et accumsan et iusto odio dignissim qui blandit illum dolore eu feugiat nulla facilisis at vero eros et accumsan et vel eum iriure dolor in hendrerit in</p>
  <a class="abs btn" style="left:249px;top:146px">READ MORE</a>
</section>

<footer class="abs footer">Copyright © 2016 Tandem K. All Rights Reserved.</footer>

</body>
</html>
```